Satchel & Sundial needs new business card design

I need a new business card design. I'm looking for out-of-the-box design which represents the freedom of being a location independent entrepreneur.
I offer coaching, retreats and trips.
I would like to see designs with and without the photo.
Colors I use are black (#000000), green (#25A796) and brown (#D7C38C)
Website satchelandsundial.example

Target Market(s)

location independent entrepreneurs, digital nomads, people looking to swap the 9 to 5 for a lifestyle business

Industry/Entity Type

Business

Contact Information for Business Card

Dorota Falkner
Your Lifestyle Business Coach, Retreat & Trip Leader
http://satchelandsundial.example
hello@satchelandsundial.example
Live a life you don't need a holiday from

Font styles to use
Serif
Sans Serif

Requirements
Must have
• One side should contain only the logo. I would also consider having the "Live a life you don't need a holiday from" on that side too (depending on how it looks)
• Please show both sides on the designs.

```html
<!DOCTYPE html>
<html lang="en">
<head>
<meta charset="utf-8">
<title>Satchel &amp; Sundial — Business Card</title>
<link rel="stylesheet" href="https://fonts.googleapis.com/css2?family=Open+Sans:wght@400;600;700&display=swap">
<style>
  :root {
    --teal: #25A796;
    --black: #000000;
    --ink: #333333;
    --paper: #ffffff;
    --stage: #2c2c2c;
    --card-w: 760px;
    --card-h: 434px;
  }
  * { box-sizing: border-box; margin: 0; padding: 0; }
  html, body {
    width: 1200px; height: 950px; overflow: hidden;
    background: var(--stage);
    font-family: "Open Sans", Arial, sans-serif;
  }
  .sheet {
    width: 1200px; height: 950px;
    display: flex; flex-direction: column; align-items: center; justify-content: center;
    gap: 40px;
  }
  .card {
    position: relative;
    width: var(--card-w); height: var(--card-h);
    overflow: hidden;
    box-shadow: 0 12px 30px rgba(0,0,0,.45);
  }
  /* Front: logo side */
  .card--front {
    background: var(--teal);
    color: var(--paper);
    display: flex; flex-direction: column; align-items: center; justify-content: center;
  }
  .card--front .wordmark { font-size: 58px; font-weight: 600; color: var(--paper); letter-spacing: 1px; }
  .social-rule {
    margin-top: 48px; width: 420px; height: 1px; background: rgba(255,255,255,.7);
    position: relative;
  }
  .social-rule .social-dots {
    position: absolute; left: 50%; top: -10px; transform: translateX(-50%);
    display: flex; gap: 6px; background: var(--teal); padding: 0 8px;
  }
  .social-dots span { width: 20px; height: 20px; background: var(--paper); border-radius: 2px; }
  .tagline { margin-top: 22px; font-size: 20px; letter-spacing: .5px; }

  /* Back: contact side */
  .card--back { background: var(--paper); }
  .card--back .swoosh { position: absolute; inset: 0; }
  .card--back .wordmark {
    position: absolute; left: 50px; top: 150px;
    font-size: 52px; font-weight: 600; color: var(--black); letter-spacing: 1px;
  }
  .contact { position: absolute; left: 50px; top: 250px; color: var(--ink); }
  .contact .name { font-size: 26px; font-weight: 700; color: var(--teal); }
  .contact .role { font-size: 18px; line-height: 1.35; }
  .contact ul { list-style: none; margin-top: 16px; }
  .contact li { display: flex; align-items: center; gap: 10px; font-size: 17px; color: #555; line-height: 1.7; }
  .contact li svg { width: 18px; height: 18px; flex: none; }
</style>
</head>
<body>
<main class="sheet">
  <section class="card card--front" aria-label="Card front">
    <div class="wordmark">Satchel &amp; Sundial</div>
    <div class="social-rule">
      <div class="social-dots"><span></span><span></span><span></span></div>
    </div>
    <p class="tagline">Live a life you don't need a holiday from</p>
  </section>

  <section class="card card--back" aria-label="Card back">
    <svg class="swoosh" viewBox="0 0 760 434" preserveAspectRatio="none" aria-hidden="true">
      <path d="M250 0 L760 0 L760 215 Q640 25 250 0 Z" fill="var(--black)"/>
      <path d="M250 0 Q640 25 760 215 L760 240 Q620 40 250 0 Z" fill="var(--teal)"/>
    </svg>
    <div class="wordmark">Satchel &amp; Sundial</div>
    <div class="contact">
      <p class="name">Dorota Falkner</p>
      <p class="role">Your Lifestyle Business Coach<br>Retreat &amp; Trip Leader</p>
      <ul>
        <li>
          <svg viewBox="0 0 18 18"><rect x="1" y="4" width="16" height="11" rx="1.5" fill="var(--teal)"/><path d="M1.5 4.8 L9 10.5 L16.5 4.8" stroke="#fff" stroke-width="1.4" fill="none"/></svg>
          hello@satchelandsundial.example
        </li>
        <li>
          <svg viewBox="0 0 18 18"><circle cx="9" cy="9" r="8" fill="var(--teal)"/><path d="M9 1.5 C5 6 5 12 9 16.5 M9 1.5 C13 6 13 12 9 16.5 M1.5 9 H16.5" stroke="#fff" stroke-width="1.1" fill="none"/></svg>
          www.satchelandsundial.example
        </li>
      </ul>
    </div>
  </section>
</main>
</body>
</html>
```